Tidal Forge - Crypto Currency Miner Powered by Renewable Energy Website

We Need Web Pages Design for Website for Crypto Currency Miner

Serivices include:
Mining Rig Sales
Housing for Rigs turnkey on renewable energy grid
Cloud Mining term packages
Updates

http://www.vaultrigsurvey.example (Competitors sites)

Target Market(s)

Investers for Mining Rigs and terms for 1,2 or 3 years of Hash rate

Industry/Entity Type

Mining

Number of Pages Required

5+ page

Font styles to use
Sans Serif

Colors
add136
9bcb3c
606060
474747
ffc214
cadf82
fbee3e
876aae
6b449b

Requirements
Must have
• Pictures of Solar, Wind and power Factor Correction units
Nice to have
• e-commerce platform so contract terms can be purchased through website
Should not have
• Heavy construction equipment

```html
<!DOCTYPE html>
<html lang="en">
<head>
<meta charset="utf-8">
<title>Tidal Forge</title>
<link href="https://fonts.googleapis.com/css2?family=Mulish:wght@400;600;700&family=Open+Sans:wght@400;600;700&display=swap" rel="stylesheet">
<style>
:root{
  --green:#8dc63f;
  --green-dark:#7ab52f;
  --amber:#ffc214;
  --red:#e3132b;
  --ink:#222222;
  --text:#474747;
  --muted:#606060;
  --panel:#efefef;
  --line:#cfcfcf;
  --white:#ffffff;
  --dark-btn:#333333;
}
*{box-sizing:border-box;margin:0;padding:0}
html,body{width:1200px;height:2880px;overflow:hidden}
body{font-family:"Open Sans",Arial,sans-serif;color:var(--text);background:var(--white);position:relative}
h1,h2,h3,.logo-name{font-family:"Mulish","Open Sans",sans-serif}

/* header */
.site-header{position:absolute;left:0;top:0;width:1200px;height:148px;background:var(--white)}
.logo{position:absolute;left:130px;top:30px;display:flex;align-items:center;gap:12px}
.logo-mark{width:52px;height:52px;border-radius:50%;background:var(--green)}
.logo-name{font-size:34px;font-weight:700;color:var(--green-dark)}
.auth{position:absolute;top:38px;height:37px;font-size:13px;font-weight:700;color:var(--white);display:flex;align-items:center;justify-content:center;letter-spacing:.3px}
.auth-login{left:881px;width:89px;background:var(--dark-btn)}
.auth-register{left:979px;width:88px;background:var(--green)}
.main-nav{position:absolute;top:104px;left:0;width:1200px;height:24px;font-size:15px;color:var(--ink)}
.main-nav span{position:absolute;transform:translateX(-50%);white-space:nowrap}
.main-nav .active{color:var(--red)}

/* hero */
.hero{position:absolute;left:0;top:148px;width:1200px;height:466px;background:linear-gradient(135deg,#3b4b63 0%,#1f2f56 40%,#4a5b70 70%,#2a3447 100%)}
.hero-box{position:absolute;left:200px;top:150px;width:798px;height:169px;background:rgba(141,198,63,.9);color:var(--white)}
.hero-box h1{position:absolute;left:0;top:16px;width:100%;text-align:center;font-size:42px;font-weight:600;line-height:50px;letter-spacing:-.4px;white-space:nowrap}
.hero-box p{position:absolute;left:0;top:72px;width:100%;text-align:center;font-size:13px;line-height:18px;white-space:nowrap;opacity:.95}
.hero-cta{position:absolute;left:305px;top:107px;width:190px;height:40px;background:var(--red);font-family:"Mulish",sans-serif;font-size:16px;font-weight:700;display:flex;align-items:center;justify-content:center}
.hero-arrow{position:absolute;top:218px}

/* common */
.section-title{position:absolute;left:0;width:1200px;text-align:center;font-size:34px;font-weight:600;color:var(--green)}
.btn{position:absolute;background:var(--amber);color:var(--ink);font-size:12px;display:flex;align-items:center;justify-content:center}
.copy{font-size:12.5px;line-height:21px;color:var(--text)}

/* welcome */
.welcome-text{position:absolute;left:130px;top:733px;width:938px;text-align:center}

/* features */
.features{position:absolute;left:0;top:950px;width:1200px;height:515px;background:linear-gradient(160deg,#b5d66a 0%,#a2c94d 50%,#b1d363 100%)}
.features h2{position:absolute;top:73px;width:1200px;text-align:center;font-size:34px;font-weight:600;color:var(--ink)}
.feature-card{position:absolute;top:137px;width:298px;height:297px;background:var(--white);text-align:center}
.feature-card svg{position:absolute;left:109px;top:26px}
.feature-card h3{position:absolute;top:126px;width:100%;font-size:21px;font-weight:600;color:var(--green)}
.feature-card p{position:absolute;left:20px;top:164px;width:258px;font-size:10.5px;line-height:17px}
.feature-card .btn{left:101px;top:231px;width:96px;height:36px}

/* how it works */
.how-media{position:absolute;left:0;top:1465px;width:601px;height:384px;background:radial-gradient(circle at 45% 30%,#2f6f78 0%,#0f2a30 45%,#060c0e 100%)}
.how-panel{position:absolute;left:601px;top:1465px;width:599px;height:384px;background:var(--panel)}
.how-panel h2{position:absolute;left:36px;top:64px;font-size:34px;font-weight:600;color:var(--green)}
.how-panel p{position:absolute;left:36px;top:114px;width:430px;font-size:10.5px;line-height:20px}
.how-panel .btn{left:36px;top:284px;width:96px;height:36px}

/* blog */
.post{position:absolute;top:1985px;width:298px;height:352px;background:var(--panel)}
.post-media{width:298px;height:192px}
.post h3{font-size:15px;font-weight:700;color:var(--ink);margin:24px 0 0 20px}
.post p{font-size:11px;line-height:17px;margin:10px 20px 0 20px}
.post .more{position:absolute;left:20px;top:318px;font-size:10px;font-weight:700;color:var(--ink);text-decoration:underline}

/* footer */
.site-footer{position:absolute;left:0;top:2481px;width:1200px;height:319px;background:var(--panel)}
.footer-title{position:absolute;top:50px;font-size:16px;color:var(--ink);letter-spacing:.3px}
.email-field{position:absolute;left:132px;top:86px;width:208px;height:39px;background:var(--white);border:1px solid var(--line);font-size:12px;color:var(--ink);padding:11px 14px}
.email-field svg{position:absolute;right:14px;top:13px}
.footer-note{position:absolute;left:132px;top:136px;font-size:11px;color:var(--muted)}
.footer-links{position:absolute;top:83px;font-size:11px;line-height:26px;color:var(--muted)}
.footer-divider{position:absolute;left:132px;top:195px;width:936px;height:1px;background:var(--line)}
.lang{position:absolute;left:132px;top:236px;width:89px;height:40px;border:1px solid #999;font-size:11px;color:var(--ink);display:flex;align-items:center;justify-content:center;gap:6px}
.social{position:absolute;top:248px;width:20px;height:20px;border-radius:50%;background:#7a7a7a}
.legal{position:absolute;left:0;top:2830px;width:1200px;text-align:center;font-size:11px;color:var(--ink)}
</style>
</head>
<body>

<header class="site-header">
  <div class="logo"><span class="logo-mark"></span><span class="logo-name">Tidal Forge</span></div>
  <div class="auth auth-login">LOG IN</div>
  <div class="auth auth-register">REGISTER</div>
  <nav class="main-nav">
    <span class="active" style="left:538px">Home</span>
    <span style="left:626px">About us</span>
    <span style="left:720px">Services</span>
    <span style="left:808px">Pricing</span>
    <span style="left:887px">News</span>
    <span style="left:960px">Blog</span>
    <span style="left:1039px">Support</span>
  </nav>
</header>

<section class="hero" role="img" aria-label="Photo of a control cabinet with rows of wired electrical contactors">
  <svg class="hero-arrow" style="left:44px" width="22" height="30" viewBox="0 0 22 30"><path d="M17 3 5 15l12 12" fill="none" stroke="#fff" stroke-width="4"/></svg>
  <svg class="hero-arrow" style="left:1136px" width="22" height="30" viewBox="0 0 22 30"><path d="M5 3l12 12L5 27" fill="none" stroke="#fff" stroke-width="4"/></svg>
  <div class="hero-box">
    <h1>Vestibulum luctus egestas fringilla</h1>
    <p>Mauris bibendum fringilla velit. Nulla in lorem at massa pellentesque posuere. Nulla tristique posuere molestie.</p>
    <div class="hero-cta">START MINING NOW</div>
  </div>
</section>

<h2 class="section-title" style="top:684px">Welcome to The Tidal Forge</h2>
<p class="copy welcome-text">Fusce nec leo ac urna pulvinar auctor. Mauris bibendum fringilla velit. Nulla in lorem at massa pellentesque posuere. Nulla tristique posuere molestie. Aliquam erat volutpat. Etiam quis aliquet risus. Duis ornare erat eget magna dapibus, in accumsan quam pharetra. Nam tempus, quam in bibendum vulputate, sapien dolor viverra nisl, vitae euismod elit turpis et nulla. Aliquam erat volutpat. Pellentesque blandit lacus eget nunc faucibus, et tincidunt eros viverra. Phasellus consequat sagittis nisi suscipit feugiat. Cras eget leo sed nunc hendrerit ultricies eu at nisl.</p>
<div class="btn" style="left:551px;top:835px;width:96px;height:37px">Read more</div>

<section class="features" role="img" aria-label="Green tinted circuit board background">
  <h2>Praesent iaculis faucibus urna sit amet</h2>
  <div class="feature-card" style="left:132px">
    <svg width="80" height="80" viewBox="0 0 80 80" fill="none" stroke="#8dc63f" stroke-width="3"><rect x="14" y="6" width="52" height="20" rx="3"/><rect x="14" y="30" width="52" height="20" rx="3"/><rect x="14" y="54" width="52" height="20" rx="3"/><circle cx="24" cy="16" r="3"/><circle cx="24" cy="40" r="3"/><circle cx="24" cy="64" r="3"/><path d="M40 16h18M40 40h18M40 64h18" stroke-dasharray="3 3"/></svg>
    <h3>Maecenas consequat</h3>
    <p>Fusce eget neque elit. Sed augue orci, elementum in magna congue, tincidunt vulputate erat. Aliquam consectetur orci molestie dictum molestie.</p>
    <div class="btn">Read more</div>
  </div>
  <div class="feature-card" style="left:451px">
    <svg width="80" height="80" viewBox="0 0 80 80" fill="none" stroke="#8dc63f" stroke-width="3"><circle cx="26" cy="28" r="16"/><circle cx="54" cy="54" r="16"/><path d="M48 10a22 22 0 0 1 18 16M62 22l4 4 4-6M32 70A22 22 0 0 1 14 54M18 58l-4-4-4 6"/></svg>
    <h3>Proin eget congue</h3>
    <p>Fusce eget neque elit. Sed augue orci, elementum in magna congue, tincidunt vulputate erat. Aliquam consectetur orci molestie dictum molestie.</p>
    <div class="btn">Read more</div>
  </div>
  <div class="feature-card" style="left:770px">
    <svg width="80" height="80" viewBox="0 0 80 80" fill="none" stroke="#8dc63f" stroke-width="3"><circle cx="40" cy="40" r="36"/><path d="M24 40l11 11 22-22"/></svg>
    <h3>Vestibulum condimentum</h3>
    <p>Fusce eget neque elit. Sed augue orci, elementum in magna congue, tincidunt vulputate erat. Aliquam consectetur orci molestie dictum molestie.</p>
    <div class="btn">Read more</div>
  </div>
</section>

<div class="how-media" role="img" aria-label="Illustration of a glowing coin above a dark circuit board"></div>
<section class="how-panel">
  <h2>How it works</h2>
  <p>Fusce sollicitudin lorem et luctus volutpat. Proin placerat dapibus gravida. In tristique tristique nulla eget hendrerit. Maecenas vel tortor accumsan quam varius imperdiet vel eget elit. Aenean facilisis tincidunt lectus, id dictum nisl luctus eget. Vivamus efficitur ex condimentum, malesuada eros eget, feugiat nibh. Sed tellus ex, imperdiet eget gravida sit amet, volutpat eget turpis. In nec ultricies est. Etiam mattis augue vehicula odio posuere, sit amet tempus lectus luctus. Nulla facilisi. Etiam vel massa elementum, bibendum tellus venenatis, feugiat massa.</p>
  <div class="btn">Read more</div>
</section>

<h2 class="section-title" style="top:1919px">Blog</h2>
<article class="post" style="left:132px">
  <div class="post-media" role="img" aria-label="Photo of a mining rig with rows of graphics cards lit in blue" style="background:linear-gradient(135deg,#1b2a6b,#3a56c8 50%,#121a3a)"></div>
  <h3>Fusce eget neque elit</h3>
  <p>Etiam quis aliquet risus. Duis ornare erat eget magna dapibus, in accumsan quam pharetra. Nam tempus, quam in bibendum vulputate.</p>
  <span class="more">MORE</span>
</article>
<article class="post" style="left:451px">
  <div class="post-media" role="img" aria-label="Photo of gold coins in front of a glowing market chart" style="background:linear-gradient(135deg,#1d2a3a,#b3692a 55%,#e3a33a)"></div>
  <h3>Praesent iaculis faucibus urna sit</h3>
  <p>Etiam quis aliquet risus. Duis ornare erat eget magna dapibus, in accumsan quam pharetra. Nam tempus, quam in bibendum vulputate.</p>
  <span class="more">MORE</span>
</article>
<article class="post" style="left:770px">
  <div class="post-media" role="img" aria-label="Photo of racks of mining hardware with red cooling fans" style="background:linear-gradient(135deg,#1a2d3a,#4b6a7a 50%,#6b2a2a)"></div>
  <h3>Maecenas consequat justo enim</h3>
  <p>Etiam quis aliquet risus. Duis ornare erat eget magna dapibus, in accumsan quam pharetra. Nam tempus, quam in bibendum vulputate.</p>
  <span class="more">MORE</span>
</article>
<div class="btn" style="left:551px;top:2362px;width:96px;height:38px">View All</div>

<footer class="site-footer">
  <div class="footer-title" style="left:132px">NEWSLETTER</div>
  <div class="email-field">Email
    <svg width="16" height="12" viewBox="0 0 16 12"><rect width="16" height="12" rx="1" fill="#222"/><path d="M1 1l7 6 7-6" fill="none" stroke="#fff" stroke-width="1.4"/></svg>
  </div>
  <div class="footer-note">Curabitur eu erat dignissim varius</div>

  <div class="footer-title" style="left:493px">LINKS</div>
  <div class="footer-links" style="left:495px">Home<br>About us<br>Services</div>
  <div class="footer-links" style="left:591px">Pricing<br>News<br>Blog</div>
  <div class="footer-links" style="left:663px">Support<br>Privacy Policy<br>Terms and conditions</div>

  <div class="footer-title" style="left:933px">CONTACT INFO</div>
  <div class="footer-links" style="left:933px">555 014 2290<br>info@tidalforge.example</div>

  <div class="footer-divider"></div>
  <div class="lang"><svg width="12" height="12" viewBox="0 0 12 12"><circle cx="6" cy="6" r="6" fill="#555"/></svg>English</div>
  <span class="social" style="left:938px"></span>
  <span class="social" style="left:988px"></span>
  <span class="social" style="left:1044px"></span>
</footer>

<div class="legal">Copyright &copy; 2018 &nbsp;The Tidal Forge. &nbsp;All rights reserved.</div>

</body>
</html>
```